2 x Digitize Logo | 2 x Business Cards | 2 x Fridge Magnets

We require 6 deliverables:
1. Residential logo redrawn (same just high quality for large print format).
2. Corporate logo redrawn (minor changes to wording and high quality for large print format).
3. New business card design for Furniture Removals (residential)
4. New business card design for Corporate Relocations (business)
5. New Fridge magnet for Furniture removals (residential)
6. New fridge magnet for Corporate Relocations (business)
1. Residential Logo
a. We require the logo to be translated into a high quality digital image with no modifications.
(see attached resilogo.jpg)
2. Residential Logo
a. We require the logo to be edited (add the word corporate relocations) be translated into a high quality digital image.
(see attached corplogo.jpg)
3. Using the resilogo please make a new business card for our business.
a. Please see the web site https://www.larkbendcarters.com.au for colours and inspiration.
b. The residential business card needs the following information:
i. Business Name (using the residential logo).
ii. Free Call: 1800 LB Cart (the L, B and Cart much be the same colour as the logo).
iii. Website: www.LarkbendCarters.com.au
iv. Address: 4/17 Ormsdale Court, VIC 3264
v. Email: cart@LarkbendCarters.com.au
vi. backof Card:
Review our service
www.PennantOrbit.com.au
Services: Local, Country, Interstate | Furniture Removals | Piano, Billiard Tables & Antiques
4. Using the corplogo please make a new business card for our business.
b. The corporate business card needs the following information:
i. Business Name (using the corporate logo).
v. Email: corporate@LarkbendCarters.com.au
vi. Back of Card:
Review our service
www.PennantOrbit.com.au
Services: Corporate relocations | Office equipment moves | Packing Service | Packing Materials
5. Using the resilogo please make a new fridge magent for our business.
b. The residential fidge magnet needs the following information:
iv. Services: Local, Country, Interstate | Furniture Removals | Piano, Billiard Tables & Antiques
6. Using the corplogo please make a new fridge magent for our business.
b. The corporate fidge magnet needs the following information:
iv. Services: Local, Country, Interstate | Corporate relocations
Target Market(s)
Residential Furniture Removals and Corporate Office relocations
Industry/Entity Type
Business
Contact Information for Business Card
Please see full brief for six items required
Requirements
Must have
- Clean simple, easy to read
Nice to have
- fresh, stand out, eye catching
Should not have
- plain, standard, boring, general

```html
<!DOCTYPE html>
<html lang="en">
<head>
<meta charset="utf-8">
<title>Larkbend Carters – Business Cards</title>
<link rel="stylesheet" href="https://fonts.googleapis.com/css2?family=Anton&family=Open+Sans:wght@400;700&family=Roboto+Condensed:wght@400;500;700&display=swap">
<style>
  :root {
    --backdrop: #cdcdcd;
    --card-dark: #2b2c2c;
    --card-light: #ffffff;
    --orange: #f2a000;
    --red: #e3241b;
    --green: #0f9140;
    --ink: #2a2a2a;
  }
  * { margin: 0; padding: 0; box-sizing: border-box; }
  html, body { width: 1200px; height: 782px; overflow: hidden; background: var(--backdrop); }
  .canvas { position: relative; width: 1200px; height: 782px; }
  .card {
    position: absolute; width: 417px; height: 252px;
    box-shadow: 6px 8px 10px rgba(0,0,0,0.18);
  }
  .card--dark { background: var(--card-dark); color: #fff; }
  .card--light { background: var(--card-light); color: var(--ink); }
  .card--resi-back { left: 165px; top: 118px; }
  .card--resi-front { left: 617px; top: 118px; }
  .card--corp-back { left: 165px; top: 411px; }
  .card--corp-front { left: 617px; top: 411px; }

  .brand {
    position: absolute; transform: translate(-50%, -50%);
    font-family: "Anton", sans-serif; text-transform: uppercase;
    white-space: nowrap; letter-spacing: 0.5px; line-height: 1;
  }
  .brand--large { font-size: 34px; color: var(--orange); left: 209px; top: 76px; }
  .brand--front { font-size: 26px; color: var(--orange); left: 107px; top: 122px; text-align: center; line-height: 1.05; }
  .brand--corp { font-size: 20px; color: var(--red); }
  .tagline {
    position: absolute; transform: translateX(-50%);
    font-family: "Open Sans", sans-serif; font-size: 9.5px; color: var(--green);
    white-space: nowrap; letter-spacing: 0.2px;
  }

  .review {
    position: absolute; left: 0; width: 100%; text-align: center;
    font-family: "Open Sans", sans-serif;
  }
  .review__label { font-size: 11.5px; color: #eee; display: flex; align-items: center; justify-content: center; gap: 12px; }
  .review__label::before, .review__label::after {
    content: ""; width: 88px; height: 2px;
    background: linear-gradient(90deg, transparent, #bdbdbd 30%, #bdbdbd 70%, transparent);
  }
  .review__url { font-size: 14.5px; color: #fff; margin-top: 4px; }
  .c-orange { color: var(--orange); font-weight: 700; }
  .c-red { color: var(--red); font-weight: 700; }
  .c-green { color: var(--green); font-weight: 700; }

  .services {
    position: absolute; left: 0; width: 100%; text-align: center;
    font-family: "Roboto Condensed", sans-serif; font-weight: 500; font-size: 11.3px; color: #fff;
    white-space: nowrap;
  }
  .services .sep { color: var(--orange); margin: 0 4px; }

  .contact { position: absolute; left: 229px; font-family: "Roboto Condensed", sans-serif; }
  .contact__name { font-family: "Anton", sans-serif; font-size: 17px; color: var(--red); letter-spacing: 0.3px; line-height: 1; font-weight: 400; }
  .contact__role { font-size: 9.5px; margin-top: 5px; }
  .contact__list { list-style: none; margin-top: 14px; font-size: 10px; }
  .contact__list li { display: flex; align-items: center; gap: 8px; height: 14.5px; white-space: nowrap; }
  .contact__list svg { width: 9px; height: 9px; flex: none; }
  .contact__address { font-size: 10px; margin-top: 5px; }
  .contact__web .c-orange, .contact__web .c-green { font-weight: 400; }
</style>
</head>
<body>
<main class="canvas">

  <section class="card card--dark card--resi-back">
    <div class="brand brand--large">Larkbend Carters</div>
    <div class="review" style="top:137px">
      <p class="review__label">Review our service</p>
      <p class="review__url">www.<span class="c-orange">Pennant</span><span class="c-red">Or</span><span class="c-green">bit</span>.com.au</p>
    </div>
    <p class="services" style="top:222px">Local, Country, Interstate<span class="sep">|</span>Furniture Removals<span class="sep">|</span>Piano, Billiard Tables &amp; Antiques</p>
  </section>

  <section class="card card--light card--resi-front">
    <div class="brand brand--front">Larkbend<br>Carters</div>
    <div class="contact" style="top:70px">
      <h2 class="contact__name">DANIEL REYES</h2>
      <p class="contact__role">Managing Director</p>
      <ul class="contact__list">
        <li><svg viewBox="0 0 10 10"><path fill="#0f9140" d="M1 3.5C1 2 2.5 1 5 1s4 1 4 2.5H7L6.5 2.5h-3L3 3.5zM2 5l1.5-1.5h3L8 5v4H2z"/></svg><span>Free Call: 1800 LB</span></li>
        <li><svg viewBox="0 0 10 10"><rect x="0.5" y="2" width="9" height="6" fill="#e3241b"/><path d="M0.5 2 5 5.5 9.5 2" stroke="#fff" stroke-width="0.9" fill="none"/></svg><span>cart@larkbendcarters.com.au</span></li>
        <li class="contact__web"><svg viewBox="0 0 10 10"><circle cx="5" cy="5" r="4.2" fill="none" stroke="#0f9140" stroke-width="1"/><path d="M0.8 5h8.4M5 0.8v8.4M2 2.6h6M2 7.4h6" stroke="#0f9140" stroke-width="0.7"/></svg><span>www.<span class="c-orange">Larkbend</span><span class="c-green">Carters</span>.com.au</span></li>
      </ul>
      <p class="contact__address">4/17 Ormsdale Court, VIC 3264</p>
    </div>
  </section>

  <section class="card card--dark card--corp-back">
    <div class="brand brand--corp" style="left:209px;top:88px">Larkbend Carters</div>
    <p class="tagline" style="left:209px;top:100px">CORPORATE RELOCATIONS</p>
    <div class="review" style="top:173px">
      <p class="review__label">Review our service</p>
      <p class="review__url">www.<span class="c-orange">Pennant</span><span class="c-red">Or</span><span class="c-green">bit</span>.com.au</p>
    </div>
    <p class="services" style="top:223px;font-size:10.9px">Corporate relocations<span class="sep">|</span>Office equipment moves<span class="sep">|</span>Packing Service<span class="sep">|</span>Packing Materials</p>
  </section>

  <section class="card card--light card--corp-front">
    <div class="brand brand--corp" style="left:107px;top:120px">Larkbend Carters</div>
    <p class="tagline" style="left:107px;top:132px">CORPORATE RELOCATIONS</p>
    <div class="contact" style="top:72px">
      <h2 class="contact__name">DANIEL REYES</h2>
      <p class="contact__role">Managing Director</p>
      <ul class="contact__list">
        <li><svg viewBox="0 0 10 10"><path fill="#0f9140" d="M1 3.5C1 2 2.5 1 5 1s4 1 4 2.5H7L6.5 2.5h-3L3 3.5zM2 5l1.5-1.5h3L8 5v4H2z"/></svg><span>Free Call: 1800 LB</span></li>
        <li><svg viewBox="0 0 10 10"><rect x="0.5" y="2" width="9" height="6" fill="#e3241b"/><path d="M0.5 2 5 5.5 9.5 2" stroke="#fff" stroke-width="0.9" fill="none"/></svg><span>corporate@larkbendcarters.com.au</span></li>
        <li class="contact__web"><svg viewBox="0 0 10 10"><circle cx="5" cy="5" r="4.2" fill="none" stroke="#0f9140" stroke-width="1"/><path d="M0.8 5h8.4M5 0.8v8.4M2 2.6h6M2 7.4h6" stroke="#0f9140" stroke-width="0.7"/></svg><span>www.<span class="c-orange">Larkbend</span><span class="c-green">Carters</span>.com.au</span></li>
      </ul>
      <p class="contact__address">4/17 Ormsdale Court, VIC 3264</p>
    </div>
  </section>

</main>
</body>
</html>
```